Business Card Design & Gift cards, Gift Cert, Donation Card

Retail Gift Store-in addition to Business Cards we'd like sequenced 2 sided Gift cards, Gift Certificate Cards, and Donation Cards.please see examples and email for clarificationlogos attached with examples-
Gift Card, Gift Certificate and Donation Card will all be same style just differant upper right title, with back side info as example.
business card, as example is single sided.
looking for additional ideas for layout

Industry/Entity Type

Business

Contact Information for Business Card

211 Newman St.East Tawas, MI 48730989.362.8730Office@BrewKrew.com

Requirements
Must have
• Blue as per example
• Logos provided
• like gradiant background

```html
<!DOCTYPE html>
<html lang="en">
<head>
<meta charset="utf-8">
<title>Tillow Marsh – Business Card &amp; Gift Certificate</title>
<link rel="stylesheet" href="https://fonts.googleapis.com/css2?family=Kalam:wght@400;700&display=swap">
<style>
  :root{
    --page:#ece8e1;
    --royal:#0b3fd0;
    --royal-deep:#0a33b8;
    --sky-top:#8cbcee;
    --sky-mid:#a9d0f2;
    --sky-pale:#c8e4f7;
    --frame-light:#a9d6f2;
    --ink:#1d3fc4;
    --label:#1b2a55;
    --line:#2b4a9a;
    --white:#ffffff;
    --art-warm:#e07a7e;
    --art-muted:#b99bb4;
  }
  *{box-sizing:border-box;margin:0;padding:0}
  html,body{width:1200px;height:864px;overflow:hidden}
  body{background:var(--page);font-family:"Kalam",cursive;position:relative}

  /* Business card (portrait) */
  .business-card{
    position:absolute;left:70px;top:112px;width:360px;height:640px;
    background:var(--royal);padding:14px;
    box-shadow:0 10px 24px rgba(0,0,0,.18);
  }
  .business-card__inner{
    width:100%;height:100%;border:4px solid var(--frame-light);
    background:linear-gradient(180deg,var(--sky-mid),var(--sky-pale));
    display:flex;flex-direction:column;
  }
  .business-card__brand{flex:1;display:flex;flex-direction:column;align-items:center;padding:26px 20px 10px}
  .brand-name{font-size:44px;font-weight:400;color:var(--ink);letter-spacing:1px;line-height:1}
  .brand-illustration{
    margin-top:18px;width:240px;height:180px;border-radius:10px;
    background:linear-gradient(160deg,var(--art-warm),var(--sky-pale));
  }
  .business-card__contact{
    height:262px;margin:0 -4px -4px;background:var(--royal-deep);
    color:var(--white);font-size:22px;line-height:1.55;font-style:normal;
    display:flex;flex-direction:column;justify-content:center;padding:0 28px;
  }

  /* Gift certificate (landscape) */
  .gift-certificate{
    position:absolute;left:480px;top:232px;width:660px;height:400px;
    background:linear-gradient(180deg,var(--sky-top) 0%,var(--sky-mid) 45%,var(--sky-pale) 100%);
    box-shadow:0 10px 24px rgba(0,0,0,.18);overflow:hidden;
  }
  .gift-certificate__art{
    position:absolute;left:10px;top:10px;width:270px;height:340px;border-radius:12px;opacity:.5;
    background:linear-gradient(180deg,var(--art-muted),rgba(185,155,180,.25));
  }
  .gift-certificate__title{
    position:absolute;left:300px;top:40px;font-size:36px;font-weight:700;color:var(--ink);
    letter-spacing:2px;line-height:1.2;white-space:nowrap;
  }
  .field{position:absolute;display:flex;align-items:flex-end;font-size:21px;line-height:1.2;color:var(--label);letter-spacing:1px;white-space:nowrap}
  .field__line{flex:1;border-bottom:1.5px solid var(--line);margin-left:8px;height:1px}
  .field--to{left:260px;top:112px;width:370px}
  .field--from{left:240px;top:156px;width:390px}
  .field--amount{left:220px;top:200px;width:410px}
  .field--number{left:30px;top:268px;width:260px}
  .field--expiration{left:230px;top:310px;width:260px}
  .field--emp{left:470px;top:350px;width:170px}
</style>
</head>
<body>
  <article class="business-card">
    <div class="business-card__inner">
      <div class="business-card__brand">
        <h1 class="brand-name">Tillow Marsh</h1>
        <div class="brand-illustration" role="img" aria-label="Brand illustration area: dancing figure over a rising sun"></div>
      </div>
      <address class="business-card__contact">
        <span class="contact-phone">989.517.4296</span>
        <span class="contact-email">Office@TillowMarsh.com</span>
        <span class="contact-street">482 Larkfield Ave.</span>
        <span class="contact-city">Pine Harbor, MI 48614</span>
      </address>
    </div>
  </article>

  <article class="gift-certificate">
    <div class="gift-certificate__art" role="img" aria-label="Faded background illustration area: dancing figure over a rising sun"></div>
    <h2 class="gift-certificate__title">GIFT CERTIFICATE</h2>
    <div class="field field--to">TO:<span class="field__line"></span></div>
    <div class="field field--from">FROM:<span class="field__line"></span></div>
    <div class="field field--amount">AMOUNT:<span class="field__line"></span></div>
    <div class="field field--number">NUMBER<span class="field__line"></span></div>
    <div class="field field--expiration">EXPIRATION<span class="field__line"></span></div>
    <div class="field field--emp">EMP<span class="field__line"></span></div>
  </article>
</body>
</html>
```